Ridgeline Journeys business card

please see website
www.ridgelinejourneys.comau

info needed on card
Curtis Halvey
Ph
email
Adventure Riding GPS trails

please use my logo and colours off my site

Curtis Halvey
curtis@ridgelinejourneys.com

```html
<!DOCTYPE html>
<html lang="en">
<head>
<meta charset="utf-8">
<title>Ridgeline Journeys – Business Card</title>
<link rel="stylesheet" href="https://fonts.googleapis.com/css2?family=Source+Sans+3:wght@400;600;700&display=swap">
<style>
  :root {
    --backdrop: #1a1a1a;
    --card: #ffffff;
    --accent-yellow: #ffcc00;
    --mark-grey: #5a5a5a;
    --faint-grey: #f1f1f1;
    --text-grey: #555555;
    --text-black: #111111;
  }
  * { margin: 0; padding: 0; box-sizing: border-box; }
  html, body { width: 1200px; height: 900px; overflow: hidden; }
  body {
    background: var(--backdrop);
    font-family: "Source Sans 3", Arial, sans-serif;
    position: relative;
  }
  .card {
    position: absolute;
    top: 170px;
    width: 347px;
    height: 561px;
    background: var(--card);
    overflow: hidden;
  }
  .card--front { left: 259px; }
  .card--back { left: 631px; }

  .accent-band {
    position: absolute;
    left: 73px;
    width: 202px;
    height: 20px;
    background: var(--accent-yellow);
  }
  .accent-band--top { top: 0; }
  .accent-band--bottom { bottom: 0; }

  .brand-name {
    position: absolute;
    font-weight: 700;
    text-transform: uppercase;
    line-height: 1.05;
  }
  .card--front .brand-name {
    top: 168px;
    left: 0; right: 0;
    text-align: center;
    font-size: 38px;
    color: var(--mark-grey);
    letter-spacing: 1px;
  }
  .card--back .brand-name {
    top: 364px;
    left: 150px;
    text-align: left;
    font-size: 28px;
    color: var(--text-black);
  }

  .backdrop-ring {
    position: absolute;
    top: 0;
    left: 0;
    width: 347px;
    height: 320px;
  }
  .brand-dot {
    position: absolute;
    top: 352px;
    left: 52px;
    width: 78px;
    height: 78px;
    border-radius: 50%;
    background: var(--mark-grey);
  }

  .holder-name {
    position: absolute;
    top: 358px;
    left: 0; right: 0;
    text-align: center;
    font-size: 19px;
    font-weight: 600;
    color: var(--accent-yellow);
  }
  .contact-list {
    position: absolute;
    top: 397px;
    left: 0; right: 0;
    list-style: none;
    text-align: center;
    font-size: 15.5px;
    color: var(--text-grey);
    line-height: 20px;
  }
  .contact-list svg {
    width: 10px; height: 10px;
    margin-right: 6px;
    vertical-align: -1px;
    fill: var(--accent-yellow);
  }
  .tagline {
    position: absolute;
    top: 474px;
    left: 0; right: 0;
    text-align: center;
    font-size: 16px;
    font-weight: 700;
    color: var(--text-black);
  }
</style>
</head>
<body>
  <section class="card card--front">
    <div class="accent-band accent-band--top"></div>
    <div class="brand-name">Ridgeline<br>Journeys</div>
    <h1 class="holder-name">Curtis Halvey</h1>
    <ul class="contact-list">
      <li><svg viewBox="0 0 10 10" aria-hidden="true"><path d="M1 3c0-1 1-2 4-2s4 1 4 2v1H7V3H3v1H1zM2 5h6l1 4H1z"/></svg>044-987 650 312</li>
      <li><svg viewBox="0 0 10 10" aria-hidden="true"><path d="M0 2h10v6H0zM1 3v.4l4 2.5 4-2.5V3L5 5.3z" fill-rule="evenodd"/></svg>curtis@ridgelinejourneys.com</li>
      <li><svg viewBox="0 0 10 10" aria-hidden="true"><path d="M4 6 6 4M3.5 4.5 2 6a1.4 1.4 0 0 0 2 2l1.5-1.5M6.5 5.5 8 4a1.4 1.4 0 0 0-2-2L4.5 3.5" fill="none" stroke="#ffcc00" stroke-width="1.3"/></svg>www.ridgelinejourneys.comau</li>
    </ul>
    <div class="accent-band accent-band--bottom"></div>
  </section>

  <section class="card card--back">
    <svg class="backdrop-ring" viewBox="0 0 347 320" aria-hidden="true">
      <circle cx="175" cy="95" r="150" fill="none" stroke="#f1f1f1" stroke-width="44"/>
    </svg>
    <div class="brand-dot" aria-hidden="true"></div>
    <div class="brand-name">Ridgeline<br>Journeys</div>
    <p class="tagline">Adventure Riding GPS trails</p>
  </section>
</body>
</html>
```